New Webpage for High Class Expert Witness Services Company

We are looking for a minimalist design for a webpage that just has our logo and an entry form offer to connect with one of our Liaisons.
The entry form should just ask for Name, Email, Contact Info and Description of Project.

Company Name is: The Marlowe Crest Advisory Services

Number of Pages Required

1 page

```html
<!DOCTYPE html>
<html lang="en">
<head>
<meta charset="utf-8">
<title>The Marlowe Crest Advisory Services — Liaison Contact Page Concepts</title>
<link rel="stylesheet" href="https://fonts.googleapis.com/css2?family=Cinzel:wght@400&family=Poppins:wght@400;600;700&display=swap">
<style>
  :root {
    --board-top: #0a2a3e;
    --board-deep: #020a17;
    --ink: #121212;
    --paper: #ffffff;
    --mist: #ececec;
    --field: #ededed;
    --field-line: #d6d6d6;
    --placeholder: #b4b4b4;
    --icon: #9d9d9d;
    --silver: #d9dadb;
    --frame: #ffffff;
  }
  * { box-sizing: border-box; margin: 0; padding: 0; }
  html, body { width: 1200px; height: 3012px; overflow: hidden; }
  body {
    position: relative;
    font-family: "Poppins", Arial, sans-serif;
    background:
      radial-gradient(ellipse 700px 260px at 50% 1000px, rgba(14,60,90,.55), transparent 70%),
      radial-gradient(ellipse 700px 260px at 50% 1640px, rgba(14,60,90,.55), transparent 70%),
      radial-gradient(ellipse 700px 260px at 50% 2270px, rgba(14,60,90,.5), transparent 70%),
      linear-gradient(180deg, var(--board-top) 0%, var(--board-deep) 14%, #041626 40%, var(--board-deep) 62%, #05213a 82%, var(--board-deep) 100%);
  }

  /* ---------- brand wordmark ---------- */
  .wordmark {
    display: flex; align-items: center; gap: 10px;
    font-family: "Cinzel", "Times New Roman", serif; font-weight: 400;
    color: var(--silver); line-height: 1.05; letter-spacing: .06em;
  }
  .wordmark__square { width: 10px; height: 10px; background: currentColor; flex: none; }
  .wordmark__name { display: block; font-size: 21px; white-space: nowrap; }
  .wordmark__line { display: block; font-size: 10px; letter-spacing: .28em; margin-top: 3px; white-space: nowrap; }

  .board-title {
    position: absolute; left: 0; top: 132px; width: 1200px;
    justify-content: center; gap: 22px;
  }
  .board-title .wordmark__square { width: 26px; height: 26px; }
  .board-title .wordmark__name { font-size: 60px; letter-spacing: .04em; }
  .board-title .wordmark__line { font-size: 26px; letter-spacing: .34em; margin-top: 12px; }

  /* ---------- screens ---------- */
  .screen {
    position: absolute; left: 179px; width: 842px; height: 555px;
    border: 4px solid var(--frame); border-radius: 22px; overflow: hidden;
    background: var(--ink);
  }
  .screen--dark { top: 399px; }
  .screen--split-band { top: 1026px; background: var(--mist); }
  .screen--side { top: 1657px; background: var(--paper); }
  .screen--camo { top: 2285px; }

  .screen .wordmark { position: absolute; }
  .screen__logo { left: 0; width: 834px; justify-content: center; top: 49px; }

  .photo { position: absolute; }
  .copyright {
    position: absolute; left: 0; width: 834px; text-align: center;
    font-size: 7px; font-weight: 700; letter-spacing: .02em; color: var(--paper);
  }

  /* ---------- form card ---------- */
  .form-card {
    position: absolute; left: 267px; width: 299px;
    background: var(--paper); border-radius: 14px; padding: 19px 27px 27px;
  }
  .field { margin-bottom: 11px; }
  .field__label {
    display: block; font-size: 7px; font-weight: 700; color: var(--ink);
    text-transform: uppercase; margin-bottom: 6px; letter-spacing: .01em;
  }
  .field__box {
    position: relative; height: 28px; border-radius: 3px; background: var(--field);
    font-size: 7.5px; color: var(--placeholder); padding: 0 11px;
    display: flex; align-items: center;
  }
  .field__box--area { height: 60px; align-items: flex-start; }
  .field__icon {
    position: absolute; right: 11px; top: 10px; width: 8px; height: 8px; fill: var(--icon);
  }
  .connect-btn {
    position: relative; display: flex; align-items: center; justify-content: center;
    height: 30px; margin-top: 16px; border-radius: 4px; background: var(--ink);
    color: var(--paper); font-size: 7px; font-weight: 700; text-transform: uppercase;
  }
  .connect-btn svg { position: absolute; right: 12px; top: 11px; width: 8px; height: 8px; fill: var(--paper); }

  /* variant: dark hero */
  .screen--dark .form-card { top: 131px; }
  .screen--dark .copyright { top: 522px; }

  /* variant: dark band on light */
  .band { position: absolute; left: 0; top: 0; width: 834px; height: 188px; background: var(--ink); }
  .screen--split-band .form-card { top: 144px; box-shadow: 0 26px 34px rgba(0,0,0,.14); }
  .screen--split-band .field__box--area { height: 76px; }
  .screen--split-band .copyright { top: 517px; color: var(--ink); }

  /* variant: side panel */
  .side-panel { position: absolute; left: 0; top: 0; width: 476px; height: 547px; background: var(--ink); }
  .screen--side .screen__logo { left: 88px; top: 98px; width: auto; }
  .screen--side .wordmark__name { font-size: 25px; }
  .screen--side .wordmark__line { font-size: 12px; }
  .screen--side .copyright { left: 82px; width: auto; top: 514px; text-align: left; }
  .side-form { position: absolute; left: 534px; top: 100px; width: 246px; }
  .side-form__title {
    font-family: "Cinzel", "Times New Roman", serif; font-weight: 400;
    font-size: 21px; line-height: 1.1; color: var(--ink); margin-bottom: 21px;
  }
  .side-form .field__box--area { height: 76px; }

  /* variant: light texture */
  .screen--camo .form-card {
    top: 83px; padding-top: 24px;
    border-top: 2px solid var(--ink); border-radius: 20px;
    box-shadow: 0 18px 30px rgba(0,0,0,.12);
  }
  .screen--camo .field__box { background: var(--paper); border: 1px solid var(--field-line); }
  .screen--camo .field__box--area { height: 76px; }
  .card-logo { position: static !important; justify-content: center; color: var(--ink); margin-bottom: 18px; gap: 6px; }
  .card-logo .wordmark__square { width: 7px; height: 7px; }
  .card-logo .wordmark__name { font-size: 14px; }
  .card-logo .wordmark__line { font-size: 6.5px; margin-top: 1px; }
</style>
</head>
<body>

<svg width="0" height="0" style="position:absolute" aria-hidden="true">
  <symbol id="i-user" viewBox="0 0 16 16"><circle cx="8" cy="4.5" r="3.5"/><path d="M1.5 16c0-4 3-6.5 6.5-6.5s6.5 2.5 6.5 6.5z"/></symbol>
  <symbol id="i-mail" viewBox="0 0 16 16"><path d="M0 3h16v2L8 10 0 5z"/><path d="M0 7l8 5 8-5v7H0z"/></symbol>
  <symbol id="i-phone" viewBox="0 0 16 16"><path d="M3.5 0.5l3 3.5-1.8 2.2c1 2 2.6 3.6 4.6 4.6L11.5 9l3.5 3-1.7 2.8C7 15 1 9 1.2 2.2z"/></symbol>
  <symbol id="i-chat" viewBox="0 0 16 16"><circle cx="9" cy="7" r="6"/><path d="M2 15l2-5 4 3z"/></symbol>
  <symbol id="i-send" viewBox="0 0 16 16"><path d="M16 0L0 7l5 2 9-7-7 8v6l3-4 4 2z"/></symbol>
</svg>

<div class="wordmark board-title">
  <span class="wordmark__square"></span>
  <span><span class="wordmark__name">MARLOWE CREST</span><span class="wordmark__line">ADVISORY SERVICES</span></span>
</div>

<!-- Concept 1: dark hero -->
<section class="screen screen--dark">
  <div class="photo" role="img" aria-label="Faded monochrome photo of an armed soldier in tactical gear" style="left:0;top:210px;width:470px;height:337px;background:radial-gradient(ellipse at 35% 55%, #2a2a2a, #151515 70%, transparent 90%);"></div>
  <div class="photo" role="img" aria-label="Dark space scene on the right side" style="left:600px;top:200px;width:234px;height:347px;background:radial-gradient(ellipse at 70% 60%, #1f1f1f, transparent 70%);"></div>
  <div class="wordmark screen__logo"><span class="wordmark__square"></span><span><span class="wordmark__name">MARLOWE CREST</span><span class="wordmark__line">ADVISORY SERVICES</span></span></div>
  <form class="form-card">
    <div class="field"><span class="field__label">Name</span><div class="field__box">Johny<svg class="field__icon"><use href="#i-user"/></svg></div></div>
    <div class="field"><span class="field__label">Email</span><div class="field__box">Johny@email.com<svg class="field__icon"><use href="#i-mail"/></svg></div></div>
    <div class="field"><span class="field__label">Contact Info</span><div class="field__box">+081 123456 789<svg class="field__icon"><use href="#i-phone"/></svg></div></div>
    <div class="field"><span class="field__label">Description of Project</span><div class="field__box field__box--area"><svg class="field__icon"><use href="#i-chat"/></svg></div></div>
    <div class="connect-btn">Connect with us<svg><use href="#i-send"/></svg></div>
  </form>
  <p class="copyright">© COPYRIGHT 2026</p>
</section>

<!-- Concept 2: dark band on light -->
<section class="screen screen--split-band">
  <div class="band"></div>
  <div class="photo" role="img" aria-label="Monochrome photo of a soldier in helmet and goggles holding a rifle" style="left:600px;top:10px;width:216px;height:178px;background:radial-gradient(ellipse 50% 55% at 50% 60%, #2e2e2e, #121212);"></div>
  <div class="wordmark screen__logo"><span class="wordmark__square"></span><span><span class="wordmark__name">MARLOWE CREST</span><span class="wordmark__line">ADVISORY SERVICES</span></span></div>
  <form class="form-card">
    <div class="field"><span class="field__label">Name</span><div class="field__box">Johny<svg class="field__icon"><use href="#i-user"/></svg></div></div>
    <div class="field"><span class="field__label">Email</span><div class="field__box">Johny@email.com<svg class="field__icon"><use href="#i-mail"/></svg></div></div>
    <div class="field"><span class="field__label">Contact Info</span><div class="field__box">+081 123456 789<svg class="field__icon"><use href="#i-phone"/></svg></div></div>
    <div class="field"><span class="field__label">Description of Project</span><div class="field__box field__box--area"><svg class="field__icon"><use href="#i-chat"/></svg></div></div>
    <div class="connect-btn">Connect with us<svg><use href="#i-send"/></svg></div>
  </form>
  <p class="copyright">© COPYRIGHT 2026</p>
</section>

<!-- Concept 3: side panel -->
<section class="screen screen--side">
  <div class="side-panel"></div>
  <div class="photo" role="img" aria-label="Faded monochrome photo of a soldier aiming a rifle" style="left:0;top:230px;width:476px;height:317px;background:radial-gradient(ellipse at 50% 55%, #262626, #151515 70%, #121212);"></div>
  <div class="wordmark screen__logo"><span class="wordmark__square"></span><span><span class="wordmark__name">MARLOWE CREST</span><span class="wordmark__line">ADVISORY SERVICES</span></span></div>
  <p class="copyright">© COPYRIGHT 2026 ALL RIGHTS RESERVED</p>
  <form class="side-form">
    <h2 class="side-form__title">THE MARLOWE CREST<br>ADVISORY SERVICES</h2>
    <div class="field"><span class="field__label">Name</span><div class="field__box">Johny<svg class="field__icon"><use href="#i-user"/></svg></div></div>
    <div class="field"><span class="field__label">Email</span><div class="field__box">Johny@email.com<svg class="field__icon"><use href="#i-mail"/></svg></div></div>
    <div class="field"><span class="field__label">Contact Info</span><div class="field__box">+081 123456 789<svg class="field__icon"><use href="#i-phone"/></svg></div></div>
    <div class="field"><span class="field__label">Description of Project</span><div class="field__box field__box--area"><svg class="field__icon"><use href="#i-chat"/></svg></div></div>
    <div class="connect-btn">Connect with us<svg><use href="#i-send"/></svg></div>
  </form>
</section>

<!-- Concept 4: light texture -->
<section class="screen screen--camo">
  <div class="photo" role="img" aria-label="Pale grey and white winter camouflage texture" style="left:0;top:0;width:834px;height:547px;background:radial-gradient(ellipse at 30% 30%, #f1f2f4, #e2e4e7 60%, #eceef0);"></div>
  <form class="form-card">
    <div class="wordmark card-logo"><span class="wordmark__square"></span><span><span class="wordmark__name">MARLOWE CREST</span><span class="wordmark__line">ADVISORY SERVICES</span></span></div>
    <div class="field"><span class="field__label">Name</span><div class="field__box">Johny<svg class="field__icon"><use href="#i-user"/></svg></div></div>
    <div class="field"><span class="field__label">Email</span><div class="field__box">Johny@email.com<svg class="field__icon"><use href="#i-mail"/></svg></div></div>
    <div class="field"><span class="field__label">Contact Info</span><div class="field__box">+081 123456 789<svg class="field__icon"><use href="#i-phone"/></svg></div></div>
    <div class="field"><span class="field__label">Description of Project</span><div class="field__box field__box--area"><svg class="field__icon"><use href="#i-chat"/></svg></div></div>
    <div class="connect-btn">Connect with us<svg><use href="#i-send"/></svg></div>
  </form>
</section>

</body>
</html>
```